Professional Photography Business cards

I need business cards that include my logo which I have uploaded. I run a photography business. I am open to ideas but I would like one side to have my logo and the other side to have my contact info. I don't have a website made but I do own a website domain. I have uploaded 2 different logo color schemes. My business colors are Blue, black , and white.

Business Name
Business Phone Number
Business Email
Business Website address
Instagram

Industry/Entity Type

Professional Photography

Contact Information for Business Card

Phone Number: 916-384-7702 email: info@tlane-studio.example Instagram: @t.lanestudio website doman- www.tlane-studio.example

Requirements
Must have
• I like the idea of a business card with a full black background front and back of card. My colors must include royal blue, black, and white

```html
<!DOCTYPE html>
<html lang="en">
<head>
<meta charset="UTF-8">
<title>T. Lane Studio – Business Cards</title>
<link rel="stylesheet" href="https://fonts.googleapis.com/css2?family=Roboto:wght@300;400&display=swap">
<style>
  :root {
    --backdrop: #0c0c0d;
    --card: #232325;
    --emboss: #2b2b2e;
    --emboss-line: #38383c;
    --royal-blue: #1a2fd0;
    --white: #f2f2f2;
    --rule: #4a4a4e;
  }
  * { box-sizing: border-box; margin: 0; padding: 0; }
  html, body {
    width: 1200px;
    height: 820px;
    overflow: hidden;
    background: var(--backdrop);
    font-family: "Roboto", Arial, sans-serif;
  }
  .sheet {
    width: 1200px;
    height: 820px;
    display: flex;
    align-items: center;
    justify-content: center;
    gap: 60px;
  }
  .card {
    position: relative;
    width: 525px;
    height: 300px;
    background: var(--card);
    border: 2px solid var(--royal-blue);
    border-radius: 3px;
    overflow: hidden;
  }

  /* Contact side */
  .card--contact .brand {
    position: absolute;
    top: 44px;
    right: 40px;
    display: flex;
    align-items: center;
    gap: 14px;
  }
  .card--contact .wordmark {
    color: var(--royal-blue);
    font-size: 32px;
    font-weight: 400;
  }
  .card--contact .brand-circle {
    width: 56px;
    height: 56px;
    border: 3px solid var(--white);
    border-radius: 50%;
  }
  .card--contact .divider {
    position: absolute;
    left: 40px;
    right: 40px;
    top: 158px;
    height: 1px;
    background: var(--rule);
  }
  .contact-list {
    position: absolute;
    left: 40px;
    bottom: 30px;
    list-style: none;
    color: var(--white);
    font-size: 17px;
    font-weight: 300;
    line-height: 27px;
  }
  .contact-list li {
    display: flex;
    align-items: center;
    gap: 10px;
  }
  .contact-list svg {
    width: 15px;
    height: 15px;
    flex: none;
  }
  .social-handle {
    position: absolute;
    right: 40px;
    bottom: 84px;
    display: flex;
    align-items: center;
    gap: 9px;
    color: var(--white);
    font-size: 17px;
    font-weight: 300;
  }
  .social-handle .dot {
    width: 14px;
    height: 14px;
    border: 1.5px solid var(--white);
    border-radius: 50%;
  }

  /* Logo side */
  .card--logo .emboss-circle {
    position: absolute;
    top: 34px;
    right: 62px;
    width: 170px;
    height: 170px;
    border-radius: 50%;
    background: var(--emboss);
    border: 6px solid var(--emboss-line);
  }
  .card--logo .wordmark {
    position: absolute;
    left: 70px;
    bottom: 56px;
    color: var(--white);
    font-size: 40px;
    font-weight: 400;
  }
</style>
</head>
<body>
<main class="sheet">
  <section class="card card--contact" aria-label="Contact side">
    <div class="brand">
      <p class="wordmark">T. Lane Studio</p>
      <span class="brand-circle"></span>
    </div>
    <div class="divider"></div>
    <ul class="contact-list">
      <li>
        <svg viewBox="0 0 16 16" aria-hidden="true"><path d="M4 1.5l2.2 3-1.3 1.6c.8 1.8 2.2 3.2 4 4l1.6-1.3 3 2.2-1.2 2.5C7.5 13.2 2.8 8.5 1.5 3.2z" fill="none" stroke="currentColor" stroke-width="1.4" stroke-linejoin="round"/></svg>
        <span>916-384-7702</span>
      </li>
      <li>
        <svg viewBox="0 0 16 16" aria-hidden="true"><rect x="1" y="3" width="14" height="10" fill="none" stroke="currentColor" stroke-width="1.4"/><path d="M1 3l7 6 7-6" fill="none" stroke="currentColor" stroke-width="1.4"/></svg>
        <span>info@tlane-studio.example</span>
      </li>
      <li>
        <svg viewBox="0 0 16 16" aria-hidden="true"><circle cx="8" cy="8" r="6.5" fill="none" stroke="currentColor" stroke-width="1.3"/><ellipse cx="8" cy="8" rx="3" ry="6.5" fill="none" stroke="currentColor" stroke-width="1.1"/><path d="M1.5 8h13M2.5 5h11M2.5 11h11" stroke="currentColor" stroke-width="1"/></svg>
        <span>www.tlane-studio.example</span>
      </li>
    </ul>
    <p class="social-handle"><span>@t.lanestudio</span><span class="dot"></span></p>
  </section>

  <section class="card card--logo" aria-label="Logo side">
    <span class="emboss-circle"></span>
    <p class="wordmark">T. Lane Studio</p>
  </section>
</main>
</body>
</html>
```